I need a complete stationary pack for a real estate office that sells and manages residential proper

We need a stationary design pack for my real estate office called ‘brightkeyhomes’ that is in Queensland Australia. My offices are both in suburban and coastal locations in the south west corner of Queensland at the Coral Bay Shore and Brisbane.
We predominately manage real estate on behalf of owners and sell property in the residential sector.
I have attached a copy of our existing design of my business card and do like the current concept/layout. In saying this you may be able to use this existing theme across to the other items required or see opportunity on how to improve what I have already.
I would like to see concepts for the following products:
- Letterhead
- Fax header
- Business cards
- Email signature
- With complements slips and
- Envelopes
I have attached our current logo that was designed by Artfolder and the font is Prelo.

I am looking for a contemporary design that is professional and reflects trust and professionalism. I am currently using the logo with a black background on some material as per the following link

http://www.plotlisting.com.au/property/for-sale/house/qld/merridale/?adid=4827305118&sp=7

I have posted another job 517362 for signage and the company car signage done too if you are interested.

Please do not hesitate to contact me should you have any questions. Thank you.

Target Market(s)

Western speaking people aged from 25 to 60 from modest backgrounds to well off individuals

Industry/Entity Type

Real Estate

Requirements
Must have
• Professional in appearance, show a mature and trustworthy image
Should not have
• As there is good colour with the logo, i am do not want over the top designs or colours

```html
<!DOCTYPE html>
<html lang="en">
<head>
<meta charset="utf-8">
<title>brightkeyhomes stationery pack</title>
<link href="https://fonts.googleapis.com/css2?family=Open+Sans:ital,wght@0,400;0,600;0,700;1,400&display=swap" rel="stylesheet">
<style>
:root{
  --bg:#e8e5e0;
  --ink:#2b2f38;
  --black:#0b0b0c;
  --white:#ffffff;
  --orange:#f39a1e;
  --red:#d6262c;
  --purple:#6e2a79;
  --green:#2f9a44;
  --blue:#1f74bb;
  --grey:#6b6b6b;
}
*{margin:0;padding:0;box-sizing:border-box}
html,body{width:1200px;height:900px;overflow:hidden}
body{background:var(--bg);font-family:"Open Sans",Arial,sans-serif;color:var(--ink);position:relative}
.piece{position:absolute;overflow:hidden;box-shadow:0 2px 6px rgba(0,0,0,.18)}
.paper{background:var(--white)}
.dark{background:var(--black);color:var(--white)}
.sweep{position:absolute;left:0;bottom:0;width:100%}
.brand{display:flex;align-items:center;gap:6px;font-weight:600;color:var(--ink);white-space:nowrap}
.dark .brand{color:var(--white)}
.brand-dot{border-radius:50%;background:var(--orange);flex:none}
.contact{font-size:6px;line-height:1.45;color:var(--ink);white-space:nowrap}
.dark .contact{color:#ddd}
.contact .icon{color:var(--red);margin-right:3px}
.photo{background:linear-gradient(160deg,#9fb3c8,#3b4a5c);flex:none}
.person-name{color:var(--red);font-weight:700}
.person-role{color:var(--green)}

/* letterhead */
.letterhead{left:18px;top:30px;width:299px;height:423px}
.letterhead .brand{position:absolute;left:30px;top:70px;font-size:15px}
.letterhead .contact{position:absolute;left:194px;top:76px}

/* folder */
.folder{left:333px;top:17px;width:318px;height:448px;background:linear-gradient(135deg,var(--orange) 0%,var(--red) 30%,var(--purple) 55%,var(--blue) 80%,var(--green) 100%)}
.folder-oval{position:absolute;left:-40px;top:118px;width:400px;height:300px;border-radius:50%;background:var(--black)}
.folder .brand{position:absolute;left:0;right:0;top:262px;justify-content:center;font-size:21px;color:var(--white)}

/* fax */
.fax{left:665px;top:42px;width:298px;height:423px}
.fax .brand{position:absolute;left:20px;top:62px;font-size:11px}
.fax .contact{position:absolute;left:193px;top:40px}
.fax-title{position:absolute;right:18px;top:96px;font-size:10px;font-weight:700;color:#555}
.fax-table{position:absolute;left:20px;top:112px;width:261px;border-collapse:collapse;font-size:5.5px}
.fax-table td{border:1px solid #555;height:13px;padding:0 3px}
.fax-table .label{width:50px}
.fax-checks{position:absolute;left:20px;top:170px;display:flex;gap:10px;font-size:5.5px}
.fax-checks span::before{content:"";display:inline-block;width:6px;height:6px;border:1px solid #777;margin-right:3px;vertical-align:-1px}

/* business cards */
.card{left:973px;width:208px}
.card-1{top:12px;height:127px}
.card-2{top:148px;height:119px}
.card-3{top:276px;height:119px}
.card-4{top:405px;height:119px}
.card .brand{position:absolute;left:12px;font-size:9px;gap:4px}
.card-1 .brand,.card-2 .brand,.card-3 .brand{top:50%;transform:translateY(-50%)}
.card-divider{position:absolute;left:106px;top:22px;bottom:22px;width:1px;background:#555}
.card-3 .card-divider{background:#ccc}
.card-info{position:absolute;left:112px;top:28px;font-size:6px}
.card-info .photo{width:26px;height:32px;display:inline-block;vertical-align:top;margin-right:4px}
.card-head{display:flex;margin-bottom:6px}
.card-head .person-name{font-size:7px}
.card-3 .person-name{color:var(--blue)}
.card-info .contact{font-size:5.2px;line-height:1.5}
.card-info .contact .icon{margin-right:2px}
.card-4 .brand{left:0;right:0;top:50px;justify-content:center;font-size:13px;gap:6px}
.card-url{position:absolute;left:0;right:0;bottom:8px;text-align:center;font-size:5.5px;color:#ccc}

/* email signature */
.signature{left:27px;top:477px;width:583px;height:136px}
.signature .brand{position:absolute;left:48px;top:52px;font-size:23px}
.sig-info{position:absolute;left:300px;top:20px;width:254px}
.sig-head{display:flex;gap:10px;padding-bottom:4px;border-bottom:1px solid #bbb}
.sig-head .photo{width:42px;height:50px}
.sig-head .person-name{font-size:10px;margin-top:10px}
.sig-head .person-role{font-size:8px}
.sig-head .mobile{font-size:9px;margin-top:4px}
.sig-info .contact{font-size:8.5px;margin-top:4px;line-height:1.35}

/* compliments slip */
.slip{left:62px;top:634px;width:474px;height:223px}
.slip .brand{position:absolute;left:56px;top:80px;font-size:16px}
.slip-title{position:absolute;right:28px;top:44px;font-size:13px;font-style:italic;color:#555}

/* envelopes */
.envelope-back{left:630px;top:538px;width:555px;height:228px}
.envelope-back .flap{position:absolute;left:0;top:0;width:100%;height:66px}
.envelope-front{left:575px;top:634px;width:527px;height:240px;background:radial-gradient(ellipse at 55% 35%,#222 0%,var(--black) 60%)}
.envelope-front .brand{position:absolute;left:64px;top:90px;font-size:17px}
.env-address{position:absolute;left:42px;top:130px;font-size:9px;color:var(--white)}
.env-window{position:absolute;left:36px;top:146px;width:182px;height:49px;border-radius:6px;background:linear-gradient(180deg,#f4f4f4,#bdbdbd);border:1px solid #999}
.env-url{position:absolute;right:28px;bottom:22px;font-size:9px;color:var(--white)}
.env-url b{color:var(--red);font-weight:400}
</style>
</head>
<body>

<svg width="0" height="0" style="position:absolute" aria-hidden="true">
  <defs>
    <linearGradient id="band" x1="0" x2="1" y1="0" y2="0">
      <stop offset="0" stop-color="#f39a1e"/>
      <stop offset=".55" stop-color="#f39a1e"/>
      <stop offset=".7" stop-color="#2f9a44"/>
      <stop offset=".85" stop-color="#1f74bb"/>
      <stop offset="1" stop-color="#6e2a79"/>
    </linearGradient>
    <linearGradient id="flap" x1="0" x2="1" y1="0" y2="0">
      <stop offset="0" stop-color="#f39a1e"/>
      <stop offset=".35" stop-color="#d6262c"/>
      <stop offset=".7" stop-color="#6e2a79"/>
      <stop offset="1" stop-color="#6e2a79"/>
    </linearGradient>
  </defs>
</svg>

<!-- Letterhead -->
<section class="piece paper letterhead">
  <div class="brand"><span class="brand-dot" style="width:12px;height:12px"></span>brightkeyhomes</div>
  <div class="contact">
    Shop 4, 212 harbour road,<br>merridale qld 4571<br>
    <span class="icon">☎</span>07 5512 0468<br>
    <span class="icon">✉</span>daniel@brightkeyhomes.com.au<br>
    <span class="icon">●</span>www.brightkeyhomes.com.au
  </div>
  <svg class="sweep" viewBox="0 0 299 110" height="110" preserveAspectRatio="none" aria-hidden="true">
    <path d="M0 0 Q40 85 160 85 Q250 85 299 0 L299 110 L0 110 Z" fill="url(#band)"/>
  </svg>
</section>

<!-- Presentation folder -->
<section class="piece folder">
  <div class="folder-oval"></div>
  <div class="brand"><span class="brand-dot" style="width:16px;height:16px"></span>brightkeyhomes</div>
</section>

<!-- Fax header -->
<section class="piece paper fax">
  <div class="brand"><span class="brand-dot" style="width:9px;height:9px"></span>brightkeyhomes</div>
  <div class="contact">
    Shop 4, 212 harbour road,<br>merridale qld 4571<br>
    <span class="icon">☎</span>07 5512 0468<br>
    <span class="icon">✉</span>daniel@brightkeyhomes.com.au<br>
    <span class="icon">●</span>www.brightkeyhomes.com.au
  </div>
  <div class="fax-title">FAX</div>
  <table class="fax-table">
    <tr><td class="label">To:</td><td></td><td class="label">From:</td><td></td></tr>
    <tr><td class="label">Fax:</td><td></td><td class="label">Pages:</td><td></td></tr>
    <tr><td class="label">Phone:</td><td></td><td class="label">Date:</td><td></td></tr>
    <tr><td class="label">Re:</td><td></td><td class="label">CC:</td><td></td></tr>
  </table>
  <div class="fax-checks">
    <span>Urgent</span><span>For Review</span><span>Please comment</span><span>Please Reply</span><span>Please Recycle</span>
  </div>
  <svg class="sweep" viewBox="0 0 298 110" height="110" preserveAspectRatio="none" aria-hidden="true">
    <path d="M0 0 Q40 85 160 85 Q250 85 298 0 L298 110 L0 110 Z" fill="url(#band)"/>
  </svg>
</section>

<!-- Business cards -->
<section class="piece dark card card-1">
  <div class="brand"><span class="brand-dot" style="width:7px;height:7px"></span>brightkeyhomes</div>
  <div class="card-divider"></div>
  <div class="card-info">
    <div class="card-head">
      <div class="photo" role="img" aria-label="Portrait photo of the principal"></div>
      <div><div class="person-name">Daniel Marsh</div><div class="person-role">Principal</div>0412555907</div>
    </div>
    <div class="contact">
      <span class="icon">●</span>shop 4, 212 harbour road,<br>merridale qld 4571<br>
      <span class="icon">☎</span>07 5512 0468<br>
      <span class="icon">✉</span>daniel@brightkeyhomes.com.au<br>
      <span class="icon">●</span>www.brightkeyhomes.com.au
    </div>
  </div>
</section>

<section class="piece dark card card-2">
  <div class="brand"><span class="brand-dot" style="width:7px;height:7px"></span>brightkeyhomes</div>
  <div class="card-divider"></div>
  <div class="card-info" style="top:32px">
    <div style="margin-bottom:6px"><div class="person-name">Daniel Marsh</div><div class="person-role">Principal</div>0412555907</div>
    <div class="contact">
      <span class="icon">●</span>shop 4, 212 harbour road,<br>merridale qld 4571<br>
      <span class="icon">☎</span>07 5512 0468<br>
      <span class="icon">✉</span>daniel@brightkeyhomes.com.au<br>
      <span class="icon">●</span>www.brightkeyhomes.com.au
    </div>
  </div>
</section>

<section class="piece paper card card-3">
  <div class="brand"><span class="brand-dot" style="width:7px;height:7px"></span>brightkeyhomes</div>
  <div class="card-divider"></div>
  <div class="card-info" style="top:22px">
    <div class="card-head">
      <div class="photo" role="img" aria-label="Portrait photo of the principal"></div>
      <div><div class="person-name">Daniel Marsh</div><div class="person-role">Principal</div>0412555907</div>
    </div>
    <div class="contact">
      <span class="icon">●</span>shop 4, 212 harbour road,<br>merridale qld 4571<br>
      <span class="icon">☎</span>07 5512 0468<br>
      <span class="icon">✉</span>daniel@brightkeyhomes.com.au<br>
      <span class="icon">●</span>www.brightkeyhomes.com.au
    </div>
  </div>
</section>

<section class="piece dark card card-4">
  <div class="brand"><span class="brand-dot" style="width:10px;height:10px"></span>brightkeyhomes</div>
  <div class="card-url">www.brightkeyhomes.com.au</div>
</section>

<!-- Email signature -->
<section class="piece paper signature">
  <div class="brand"><span class="brand-dot" style="width:18px;height:18px"></span>brightkeyhomes</div>
  <div class="sig-info">
    <div class="sig-head">
      <div class="photo" role="img" aria-label="Portrait photo of the principal"></div>
      <div>
        <div class="person-name">Daniel Marsh</div>
        <div class="person-role">Principal</div>
        <div class="mobile"><span style="color:var(--red)">▯</span> 0412555907</div>
      </div>
    </div>
    <div class="contact">
      Shop 4, 212 harbour road, merridale qld 4571<br>
      <span class="icon">☎</span>07 5512 0468<br>
      <span class="icon">✉</span>daniel@brightkeyhomes.com.au<br>
      <span class="icon">●</span>www.brightkeyhomes.com.au
    </div>
  </div>
</section>

<!-- With compliments slip -->
<section class="piece paper slip">
  <div class="brand"><span class="brand-dot" style="width:13px;height:13px"></span>brightkeyhomes</div>
  <div class="slip-title">With Compliments</div>
  <svg class="sweep" viewBox="0 0 474 110" height="110" preserveAspectRatio="none" aria-hidden="true">
    <path d="M0 0 Q80 80 260 80 Q400 80 474 0 L474 110 L0 110 Z" fill="url(#band)"/>
  </svg>
</section>

<!-- Envelopes -->
<section class="piece dark envelope-back">
  <svg class="flap" viewBox="0 0 555 66" preserveAspectRatio="none" aria-hidden="true">
    <rect width="555" height="66" fill="url(#flap)"/>
  </svg>
</section>

<section class="piece dark envelope-front">
  <div class="brand"><span class="brand-dot" style="width:14px;height:14px"></span>brightkeyhomes</div>
  <div class="env-address">Shop 4, 212 harbour road, merridale qld 4571</div>
  <div class="env-window"></div>
  <div class="env-url">www.<b>brightkeyhomes</b>.com.au</div>
</section>

</body>
</html>
```